Business card for event manager / organizer "waiter service"

Draft of a new valuable business card for my company.
Events, personnel service providers, festivals

```html
<!DOCTYPE html>
<html lang="de">
<head>
<meta charset="utf-8">
<title>Brenner's Kellnerservice – Visitenkarte</title>
<link href="https://fonts.googleapis.com/css2?family=Russo+One&family=Questrial&display=swap" rel="stylesheet">
<style>
  :root {
    --page: #d9d7d5;
    --card: #29252a;
    --orange: #d2611c;
    --orange-dark: #9a3e12;
    --white: #f4f2f0;
    --muted: #b9b3b0;
  }
  * { box-sizing: border-box; margin: 0; padding: 0; }
  html, body { width: 1200px; height: 874px; overflow: hidden; }
  body {
    background: var(--page);
    font-family: "Questrial", sans-serif;
    display: flex; flex-direction: column; align-items: center; justify-content: center;
    gap: 40px;
  }
  .card {
    position: relative;
    width: 600px; height: 375px;
    background: var(--card);
    border-radius: 22px;
    overflow: hidden;
    box-shadow: 0 6px 18px rgba(0,0,0,.25);
  }
  /* Front */
  .card--front { display: flex; align-items: center; justify-content: center; }
  .brand { display: flex; align-items: center; gap: 16px; }
  .brand__mark { width: 70px; height: 70px; background: var(--orange); flex: none; }
  .brand__name {
    font-family: "Russo One", sans-serif; color: var(--white);
    font-size: 34px; line-height: 1.05;
  }
  .brand__tagline { font-size: 13px; color: var(--muted); margin-top: 8px; letter-spacing: .3px; }
  /* Back */
  .photo-area { position: absolute; left: 0; top: 0; width: 290px; height: 375px; }
  .back-info {
    position: absolute; right: 34px; top: 34px;
    text-align: right; color: var(--white);
  }
  .brand--small { justify-content: flex-end; gap: 10px; }
  .brand--small .brand__mark { width: 40px; height: 40px; }
  .brand--small .brand__name { font-size: 19px; }
  .brand--small .brand__tagline { font-size: 8px; margin-top: 4px; }
  .person__name {
    font-family: "Russo One", sans-serif; color: var(--orange);
    font-size: 24px; margin-top: 22px; letter-spacing: .5px;
  }
  .person__role { font-size: 17px; margin-top: 2px; }
  .address { font-size: 16px; margin-top: 14px; }
  .contacts { list-style: none; margin-top: 14px; font-size: 15.5px; line-height: 1.35; }
  .contacts li { display: flex; justify-content: flex-end; align-items: center; gap: 10px; }
  .icon { width: 13px; height: 13px; flex: none; fill: var(--orange); }
</style>
</head>
<body>

<section class="card card--front">
  <div class="brand">
    <span class="brand__mark"></span>
    <div>
      <div class="brand__name">BRENNER'S<br>KELLNERSERVICE</div>
      <div class="brand__tagline">…weil jedes Fest gute Gastgeber braucht!</div>
    </div>
  </div>
</section>

<section class="card card--back">
  <svg class="photo-area" viewBox="0 0 290 375" role="img" aria-label="Portraitfoto des Inhabers in Kellnerweste mit zwei Sektgläsern vor orangefarbener Fläche">
    <defs>
      <linearGradient id="accent" x1="0" y1="0" x2="1" y2="1">
        <stop offset="0" stop-color="var(--orange-dark)"/>
        <stop offset="1" stop-color="var(--orange)"/>
      </linearGradient>
      <linearGradient id="portrait" x1="0" y1="0" x2="0" y2="1">
        <stop offset="0" stop-color="#3a2c26"/>
        <stop offset=".3" stop-color="#c9a894"/>
        <stop offset=".55" stop-color="#1d1b1d"/>
        <stop offset="1" stop-color="#e9e7e5"/>
      </linearGradient>
    </defs>
    <polygon points="0,50 150,25 270,220 210,375 0,375" fill="url(#accent)"/>
    <polygon points="0,150 120,60 200,110 230,375 0,375" fill="url(#portrait)"/>
  </svg>

  <div class="back-info">
    <div class="brand brand--small">
      <span class="brand__mark"></span>
      <div>
        <div class="brand__name">BRENNER'S<br>KELLNERSERVICE</div>
        <div class="brand__tagline">…weil jedes Fest gute Gastgeber braucht!</div>
      </div>
    </div>
    <div class="person__name">JONAS BRENNER</div>
    <div class="person__role">Inhaber</div>
    <div class="address">Lindenweg 12, 48153 Münster</div>
    <ul class="contacts">
      <li>0251 274 58 31
        <svg class="icon" viewBox="0 0 24 24"><path d="M6.6 10.8a15 15 0 0 0 6.6 6.6l2.2-2.2a1 1 0 0 1 1-.25 11.4 11.4 0 0 0 3.6.57 1 1 0 0 1 1 1V20a1 1 0 0 1-1 1A17 17 0 0 1 3 4a1 1 0 0 1 1-1h3.5a1 1 0 0 1 1 1c0 1.25.2 2.450.57 3.57a1 1 0 0 1-.25 1z"/></svg></li>
      <li>0171 482 73 16
        <svg class="icon" viewBox="0 0 24 24"><path d="M6.6 10.8a15 15 0 0 0 6.6 6.6l2.2-2.2a1 1 0 0 1 1-.25 11.4 11.4 0 0 0 3.6.57 1 1 0 0 1 1 1V20a1 1 0 0 1-1 1A17 17 0 0 1 3 4a1 1 0 0 1 1-1h3.5a1 1 0 0 1 1 1c0 1.25.2 2.450.57 3.57a1 1 0 0 1-.25 1z"/></svg></li>
      <li>info@brenner-kellnerservice.de
        <svg class="icon" viewBox="0 0 24 24"><path d="M2 5h20v14H2z M2 5l10 8 10-8" fill="none" stroke="var(--orange)" stroke-width="2.4"/></svg></li>
      <li>www.brenner-kellnerservice.de
        <svg class="icon" viewBox="0 0 24 24"><circle cx="12" cy="12" r="9" fill="none" stroke="var(--orange)" stroke-width="2.4"/><path d="M3 12h18M12 3c3 3 3 15 0 18M12 3c-3 3-3 15 0 18" fill="none" stroke="var(--orange)" stroke-width="1.8"/></svg></li>
      <li>brenner-kellnerservice
        <svg class="icon" viewBox="0 0 24 24"><circle cx="12" cy="12" r="11"/></svg></li>
    </ul>
  </div>
</section>

</body>
</html>
```